Modified Business card

We have developed a new logo for the business, and want thou to tray and incorporate it into the business card design that you have done for us.

I am going to upload the logo files. We like the simple clean look that you have on the card, so if you can keep the look incorporating the logo.

Industry/Entity Type

Business

```html
<!DOCTYPE html>
<html lang="en">
<head>
<meta charset="utf-8">
<title>Meridian Engineering – Business Card</title>
<link href="https://fonts.googleapis.com/css2?family=Source+Sans+3:wght@400;600;700&display=swap" rel="stylesheet">
<style>
  :root {
    --brand-red: #cf1f26;
    --ink-grey: #58595b;
    --card-edge: #2b2b2b;
    --paper: #ffffff;
  }
  html, body {
    margin: 0;
    padding: 0;
    width: 1200px;
    height: 1000px;
    overflow: hidden;
    background: var(--paper);
    font-family: "Source Sans 3", sans-serif;
  }
  .canvas {
    position: relative;
    width: 1200px;
    height: 1000px;
  }
  .card {
    position: absolute;
    left: 214px;
    width: 771px;
    height: 439px;
    border: 1px solid var(--card-edge);
    background: var(--paper);
    overflow: hidden;
  }
  .card--front { top: 46px; }
  .card--back { top: 511px; }

  /* Front */
  .front-brand {
    position: absolute;
    inset: 0;
    display: flex;
    align-items: center;
    justify-content: center;
    gap: 22px;
  }
  .front-brand__dot {
    width: 70px;
    height: 70px;
    border-radius: 50%;
    background: var(--brand-red);
  }
  .front-brand__name {
    font-size: 78px;
    font-weight: 700;
    color: var(--brand-red);
    letter-spacing: -0.5px;
  }

  /* Back header */
  .back-brand {
    position: absolute;
    left: 32px;
    top: 36px;
    display: flex;
    align-items: center;
    gap: 16px;
  }
  .back-brand__square {
    width: 97px;
    height: 97px;
    border-radius: 6px;
    background: var(--brand-red);
  }
  .back-brand__name {
    font-size: 46px;
    font-weight: 600;
    color: var(--ink-grey);
  }

  /* Red band */
  .info-band {
    position: absolute;
    left: 0;
    top: 164px;
    width: 771px;
    height: 276px;
    background: var(--brand-red);
    border-top-right-radius: 44px;
    color: var(--paper);
  }
  .person {
    position: absolute;
    right: 32px;
    top: 16px;
    text-align: right;
  }
  .person__name {
    font-size: 31px;
    font-weight: 700;
    line-height: 40px;
  }
  .person__title {
    font-size: 27px;
    font-weight: 400;
    line-height: 36px;
  }
  .postal {
    position: absolute;
    left: 32px;
    top: 120px;
    font-size: 22px;
    font-weight: 700;
    line-height: 32.5px;
  }
  .postal__web { margin-top: 3px; }
  .contacts {
    position: absolute;
    right: 32px;
    top: 114px;
    text-align: right;
    font-size: 25px;
    font-weight: 400;
    line-height: 35px;
  }
  .contacts__label {
    display: inline-block;
    margin-right: 12px;
  }
</style>
</head>
<body>
<main class="canvas">

  <section class="card card--front" aria-label="Business card front">
    <div class="front-brand">
      <span class="front-brand__dot"></span>
      <span class="front-brand__name">Meridian</span>
    </div>
  </section>

  <section class="card card--back" aria-label="Business card back">
    <header class="back-brand">
      <span class="back-brand__square"></span>
      <span class="back-brand__name">Meridian Engineering</span>
    </header>

    <div class="info-band">
      <div class="person">
        <div class="person__name">Daniel Marsh</div>
        <div class="person__title">SENIOR PROJECT MANAGER</div>
      </div>

      <address class="postal" style="font-style: normal;">
        <div>PO Box 2208,</div>
        <div>Rivermead, 7420</div>
        <div>South Africa</div>
        <div class="postal__web">www.meridianeng.co.za</div>
      </address>

      <div class="contacts">
        <div><span class="contacts__label">m</span>+27 (021) 555 0142</div>
        <div><span class="contacts__label">d</span>+27 (021) 555 0178</div>
        <div><span class="contacts__label">f</span>+27 (021) 555 0193</div>
        <div>dmarsh@meridianeng.co.za</div>
      </div>
    </div>
  </section>

</main>
</body>
</html>
```